Flyer für Verkauf von Radondetektoren
Zielgruppe
Ich verkaufe Radondetektoren zur Messung von Radon in Innenräumen. Zielgruppe sind Privatpersonen, Firmen, Genossenschaften und andere Hauseigentümer.
Aufgabenstellung
Ich brauche das Design für meine Messanleitung.
Kreativ - modern - weniger kann mehr sein
Struktur ist wichtigt, es soll also einfach sein zu lesen und zu verstehen, was gemacht werden soll. Können Bulletpoints, Icons mit eingebracht werden.
Wichtig ist auch, dass die beiden Logos 'Luftprüfer.de' und TESTOVAL' auf der Messanleitung vorhanden sind. Wobei 'Luftprüfer.de' das Hauptlogo ist.
DIN format dachte ich A4 beidseitig (Text müsste also auf diese Grösse angepasst werden).
Kann natürlich auch Flyer-Format sein oder andere Vorschläge!
Bildmaterial gibt es auf unsere Homepage https://luftprüfer.de und https://luftkontroll.se . Diese haben wir bereits gekauft und können verwendet werden. Ich lade sie den bei Bedarf hoch. Es können natürlich auch andere Vorschläge kommen.

```html
<!DOCTYPE html>
<html lang="de">
<head>
<meta charset="utf-8">
<title>Messanleitung – Luftprüfer.de</title>
<link rel="stylesheet" href="https://fonts.googleapis.com/css2?family=Open+Sans:ital,wght@0,400;0,600;0,700;1,400;1,700&family=Oswald:wght@600&display=swap">
<style>
:root{
  --bg:#ececec;
  --paper:#ffffff;
  --red:#d7262e;
  --ink:#2b2b2b;
  --text:#4a4a4a;
  --photo-lab-a:#f4f6f8;
  --photo-lab-b:#b9cbd8;
  --photo-family-a:#f3e9df;
  --photo-family-b:#d9a468;
  --partner:#1f4e9c;
}
*{box-sizing:border-box;margin:0;padding:0}
html,body{width:1200px;height:800px;overflow:hidden;background:var(--bg)}
body{font-family:"Open Sans",Arial,sans-serif;color:var(--text);position:relative}
.page{position:absolute;top:15px;width:545px;height:770px;background:var(--paper);box-shadow:0 6px 18px rgba(0,0,0,.12);overflow:hidden}
.page--front{left:40px}
.page--back{left:615px}
.footer{position:absolute;left:0;right:0;bottom:0;height:30px;background:var(--red);color:#fff;font-size:7.6px;font-weight:700;display:flex;align-items:center;justify-content:center}

/* front header */
.hero-photo{position:absolute;right:0;top:0;width:245px;height:225px;background:linear-gradient(135deg,var(--photo-lab-a) 0%,var(--photo-lab-b) 100%)}
.hero-photo::before{content:"";position:absolute;inset:0;background:linear-gradient(90deg,#fff 0%,rgba(255,255,255,0) 35%)}
.brand{position:absolute;left:26px;top:36px;display:flex;align-items:center;gap:8px}
.brand__mark{width:26px;height:26px;border-radius:50%;background:var(--ink)}
.brand__name{font-size:28px;font-weight:400;color:var(--ink);line-height:1}
.title{position:absolute;left:26px;top:100px;font-family:"Oswald","Arial Narrow",sans-serif;font-weight:600;font-size:40px;color:var(--red);letter-spacing:.5px;line-height:1}
.subtitle{position:absolute;left:26px;top:158px;font-size:15px;line-height:1.4;color:var(--ink)}

.cols{position:absolute;left:26px;right:22px;display:grid;grid-template-columns:1fr 1fr;column-gap:30px}
.page--front .cols{top:236px;bottom:38px}
.page--back .cols{top:22px;height:515px}
.col{position:relative}
.col + .col::before{content:"";position:absolute;left:-16px;top:0;bottom:0;width:2px;background:var(--red)}

.step-tag{display:inline-block;background:var(--red);color:#fff;font-size:9.6px;font-weight:600;padding:2px 6px;border-radius:2px;letter-spacing:.3px}
.step-title{font-size:8.4px;font-weight:700;color:var(--ink);margin:3px 0 6px;line-height:1.6}
p,li{font-size:6.7px;line-height:1.75}
p{margin-bottom:6px}
.link,.hl{color:var(--red);font-weight:700}
.note{font-style:italic}
.sub-underline{font-size:8px;font-weight:700;font-style:italic;color:var(--ink);text-decoration:underline;margin:10px 0 8px}
.group-head{display:flex;justify-content:space-between;align-items:center;gap:6px;font-size:8.6px;font-weight:600;color:var(--red);line-height:1.45;margin-bottom:6px}
.group-head svg{flex:none;width:28px;height:28px}
.sub-red{font-size:10px;font-weight:600;color:var(--red);margin:8px 0 5px}
ul{list-style:none;margin-bottom:10px}
li{position:relative;padding-left:15px;margin-bottom:5px}
li::before{content:"";position:absolute;left:2px;top:3px;width:6px;height:6px;border-radius:50%;background:var(--red)}
.block{margin-bottom:14px}
.spacer-lg{height:14px}
.spacer-sm{height:8px}
.red{color:var(--red)}
.strong-ink{font-weight:700;color:var(--ink)}

.address{display:flex;gap:9px;align-items:center;margin:8px 0 12px}
.address svg{width:28px;height:20px;flex:none}
.address div{font-size:7.6px;font-weight:700;color:var(--red);line-height:1.55}

.family-photo{position:absolute;left:0;right:0;top:545px;bottom:30px;background:linear-gradient(180deg,#fff 0%,var(--photo-family-a) 25%,var(--photo-family-b) 100%)}
.partner{position:absolute;right:38px;top:560px;display:flex;align-items:center;gap:6px}
.partner__mark{width:10px;height:10px;background:var(--partner)}
.partner__name{font-size:18px;color:var(--partner)}
</style>
</head>
<body>

<section class="page page--front">
  <div class="hero-photo" role="img" aria-label="Foto: zwei Laborfachkräfte in weißen Kitteln am Mikroskop"></div>
  <div class="brand"><span class="brand__mark"></span><span class="brand__name">Luftprüfer.de</span></div>
  <h1 class="title">MESSANLEITUNG</h1>
  <div class="subtitle">Für radonmessungen von innenraumluft<br>mit passiven radon detektoren</div>

  <div class="cols">
    <div class="col">
      <div class="block">
        <span class="step-tag">SCHRITT 1:</span>
        <div class="step-title">REGISTRIERUNG UND ANMELDUNG</div>
        <p>Wenn Sie Neukunde sind, legen Sie bitte zunächst ein neues Benutzerkonto auf unserem Online-Portal <span class="link">https://kundenportal.testoval.de</span> an. Anschließend können Sie die Radondetektoren registrieren. Vermerken Sie den Start der Messung (Datum und Uhrzeit), die Messorte (Raum und Etage) sowie die 9-stellige Seriennummer der Detektoren, die Sie auf der Verpackung oder auf der Unterseite der jeweiligen Detektoren finden.</p>
        <p class="note">Firmenkunden haben die Möglichkeit eine Excel-Datei als Hilfsmittel herunterzuladen, die Sie ausfüllen und dann wieder hochladen.</p>
      </div>
      <div class="block">
        <span class="step-tag">SCHRITT 2:</span>
        <div class="step-title">PLATZIERUNG DER DETEKTOREN</div>
        <p>Bevor Sie die Detektoren der Verpackung entnehmen, überlegen Sie wo genau Sie die Radondetektoren platzieren wollen. Die Radonmessung beginnt, sobald Sie die radondichten Verpackungen öffnen. Beachten Sie bei der Platzierung zunächst die <span class="hl">Auswahl der Räume</span> und <span class="hl">die Positionierung der Radondetektoren im Raum.</span> Für eine zuverlässige Radonmessung empfehlen wir wie folgt vorzugehen:</p>
        <div class="sub-underline">Die Auswahl der Räume:</div>
        <div class="group-head">Radonmessungen für Einfamilienhäuser:
          <svg viewBox="0 0 28 28" fill="none" stroke="#d7262e" stroke-width="1.4"><path d="M3 13 14 4l11 9"/><path d="M6 11v14h16V11"/><rect x="9" y="17" width="4" height="8"/><rect x="16" y="15" width="4" height="4"/></svg>
        </div>
        <ul>
          <li>Es sollten mindestens zwei Wohnräume und pro bewohnte Etage mindestens ein Wohnraum gemessen werden. Wählen Sie Räume aus, in denen Sie sich oft aufhalten (z.B. das Wohn- und Schlafzimmer). Vermeiden Sie aber Räume, in denen das Fenster mehrere Stunden am Tag oder in der Nacht geöffnet ist.</li>
          <li>Insofern Sie einen Keller haben, empfehlen wir alle Kellerräume zu messen, da hier meist das größte Risiko einer erhöhten Radonkonzentration erwartet wird.</li>
        </ul>
      </div>
    </div>

    <div class="col">
      <div class="group-head">Radonmessungen für Mehrfamilienhäuser,<br>Wohnungen und Wohnkomplexen:
        <svg viewBox="0 0 28 28" fill="none" stroke="#d7262e" stroke-width="1.4"><rect x="6" y="3" width="16" height="23"/><path d="M9 7h3M16 7h3M9 11h3M16 11h3M9 15h3M16 15h3M9 19h3M16 19h3M12 26v-4h4v4M2 26h24"/></svg>
      </div>
      <ul>
        <li>Alle Wohnungen mit direktem Bodenkontakt sowie mindestens eine Wohnung pro Etage sollten gemessen werden. Wählen Sie dabei Wohnungen, die an Aufzügen oder Luftschächten liegen.</li>
        <li>In größeren Wohnkomplexen sollten insgesamt mindestens 20% aller Wohnungen in einem Gebäude gemessen werden.</li>
        <li>Es sollten mindestens zwei Wohnräume pro ausgewählte Wohnung gemessen werden. Wählen Sie Räume aus, in denen Sie sich oft aufhalten (z.B. das Wohn- und Schlafzimmer). Vermeiden Sie aber Räume, in denen das Fenster mehrere Stunden am Tag oder in der Nacht geöffnet ist.</li>
        <li>Selbst bei einer Einzimmerwohnung sollten Sie zwei Detektoren aufstellen.</li>
      </ul>
      <div class="group-head">Radonmessungen für Arbeitsplätze und<br>öffentliche Gebäude:
        <svg viewBox="0 0 28 28" fill="none" stroke="#d7262e" stroke-width="1.4"><path d="M3 10 14 3l11 7z"/><path d="M5 10v15h18V10M8 13v9M12 13v9M16 13v9M20 13v9M2 25h24"/></svg>
      </div>
      <ul>
        <li>Wählen Sie Räume, die regelmäßig mehr als vier Stunden pro Tag genutzt werden.</li>
        <li>Messen Sie alle unterirdischen Räumlichkeiten, da hier meist das größte Risiko einer erhöhten Radonkonzentration erwartet wird.</li>
        <li>Messen Sie alle Räume im Erdgeschoß. Für größere Räumlichkeiten empfehlen wir einen Detektor pro 200 m².</li>
        <li>In den oberen Etagen sollten Sie mit mindestens zwei Detektoren, sowie mindestens einem Detektor pro 200 m² messen.</li>
      </ul>
      <div class="sub-underline">Platzierung der Detektoren im Raum:</div>
      <ul>
        <li>Platzieren Sie die Detektoren in einem Mindestabstand von 20 cm zu Wänden, 50 cm zu Abluftsventilen, sowie 1,50 m zu Fenstern, Außentüren, Zuluftsventilen und Heizkörpern.</li>
        <li>Stellen Sie die Detektoren nicht auf den Boden, an starken Wärmequellen oder Luftströmen auf. Vermeiden Sie auch Räume mit hoher Luftfeuchtigkeit, wie zum Beispiel das Badezimmer.</li>
      </ul>
    </div>
  </div>
  <div class="footer">Datenschutz (GDPR), Impressum und AGBs: Mehr Information dazu finden Sie unter www.luftprüfer.de</div>
</section>

<section class="page page--back">
  <div class="cols">
    <div class="col">
      <ul>
        <li>Die Detektoren können entweder stehend (auf einem Tisch, im Regal oder einer Schrankwand) oder hängend mitten im Raum (z.B. von einer Lampe) platziert werden.</li>
        <li>Stellen Sie die Detektoren während der gesamten Messdauer nicht um.</li>
        <li>Versuchen Sie nicht das Gehäuse der Detektoren zu öffnen und platzieren Sie diese immer außer Reichweite von Kindern.</li>
      </ul>
      <div class="spacer-lg"></div>
      <span class="step-tag">SCHRITT 3:</span>
      <div class="step-title">RADONMESSUNG</div>
      <p>Die Radonmessung beginnt, sobald Sie die radondichten Verpackungen öffnen. <span class="red">Bitte halten Sie die Messdauer wie folgt ein:</span></p>
      <div class="sub-red">Kurzzeitmessung:</div>
      <ul>
        <li>Mindestmessdauer 10 Tage (bis hin zu 30 Tagen).</li>
        <li>Führen Sie die Messung vorzugsweise in der Heizperiode (1. Oktober – 30. April) durch.</li>
        <li>Kurzzeitmessungen werden oft beim Kauf oder Verkauf von Immobilien genutzt, um ein mögliches Gefährdungspotential abschätzen zu können, oder wenn die Zeit nicht ausreicht, um eine Langzeitmessung durchzuführen.</li>
      </ul>
      <div class="sub-red">Langzeitmessung:</div>
      <ul>
        <li>Mindestmessdauer 3 Monate während der Heizperiode (1. Oktober – 30. April).</li>
        <li>Um einen Jahresmittelwert der Radonkonzentration in Innenräumen ermitteln zu können, halten Sie die Messdauer von 12 Monaten ein.</li>
        <li class="hl">Falls Ihr Arbeitsplatz in einem Radon-Vorsorgegebiet liegt und somit der Messpflicht unterliegt, muss die Messdauer von 12 Monaten eingehalten werden.</li>
      </ul>
    </div>

    <div class="col">
      <span class="step-tag">SCHRITT 3:</span>
      <div class="step-title">ABSCHLUSS DER RADONMESSUNG MIT<br>ABSCHLIESSENDEM PRÜFBERICHT</div>
      <p>Nach Ablauf der Messdauer, loggen Sie sich auf <span class="link">https://kundenportal.testoval.de</span> in Ihrem Account ein. Vermerken Sie hier das Ende der Messung und senden Sie anschließend alle Radondetektoren ausreichend frankiert in einem Umschlag oder einem Karton <span class="hl">zeitnah</span> an unsere Rücksendeadresse:</p>
      <div class="address">
        <svg viewBox="0 0 28 20" fill="none" stroke="#d7262e" stroke-width="1.8"><rect x="1" y="1" width="26" height="18" rx="1"/><path d="M1 1l13 10L27 1M1 19l10-9M27 19l-10-9"/></svg>
        <div>Luftprüfer.de<br>Lindenstraße 14 – 21614<br>Buxtehude – Deutschland</div>
      </div>
      <p>Sobald die Radondetektoren im Labor von Testoval eingetroffen sind, werden diese fachgerecht analysiert und die Ergebnisse der Radonmessung ausgewertet. Ein vollständiger Prüfbericht wird Ihnen innerhalb 36 Stunden nach Erhalt der Detektoren im Labor per E-Mail zugeschickt.</p>
      <div class="spacer-sm"></div>
      <span class="step-tag">Weitere Hinweise:</span>
      <ul style="margin-top:9px">
        <li>Bitte beachten Sie, dass die Radonmessung innerhalb von 15 Monaten nach Kaufdatum abgeschlossen sein muss.</li>
        <li>Versuchen Sie nicht das Gehäuse der Detektoren zu öffnen und platzieren Sie diese immer außer Reichweite von Kindern.</li>
        <li>Während der gesamten Messdauer dürfen die Detektoren nicht an einem anderen Ort umplatziert werden.</li>
        <li>Durch die Anmeldung auf der Website <span class="strong-ink">https://kundenportal.testoval.de</span> und die Eingabe der erforderlichen Daten bestätigt der/die Wohnungseigentümer*in/Messverantwortliche, dass er/sie die Messanleitung befolgt hat und die Detektoren gemäß den Anweisungen korrekt platziert wurden.</li>
      </ul>
    </div>
  </div>
  <div class="family-photo" role="img" aria-label="Foto: fröhliche Familie mit Hund zwischen Umzugskartons in einer hellen Wohnung"></div>
  <div class="partner"><span class="partner__mark"></span><span class="partner__name">TESTOVAL</span></div>
  <div class="footer">Datenschutz (GDPR), Impressum und AGBs: Mehr Information dazu finden Sie unter www.luftprüfer.de</div>
</section>

</body>
</html>
```